Website improvements and Adding Functionalities at https://mervo.site/tarnovex

1.Search functionality
2.Payment process functionality
3. Application configuration
4. Registration functionality activation
5. Chat functionality
6.Language switching functionality (Portuguese & French)
7.Bespoke interactive modules
8. Automated web scraping and data synchronisation mechanisms
9. News Page
10.Webinar facilities
11. Basic SEO optimisation
12. Speed and performance optimisation
13. Security configuration
14. Google Analytics integration
15. Cross-browser and mobile testing
16. Website deployment and launch support

Target Market(s)

My target markets are companies, investors, suppliers and professionals with an interest in the Mozambican oil and gas sector

Industry/Entity Type

Oil and Gas

Coding

Coded - Design and coding required

Number of Pages Required

1 page

Requirements
Must have
• Improve the existing page at https://mervo.site/tarnovex and add the following features to it: 1. Search functionality 2. Payment process functionality 3. Application configuration 4. Activation of registration functionality 5. Chat functionality 6. Language switching functionality (Portuguese & French) 7. Bespoke interactive modules 8. Automated web scraping and data synchronisation mechanisms 9. News Page

```html
<!DOCTYPE html>
<html lang="en">
<head>
<meta charset="UTF-8">
<title>Tarnovex – Mozambique Oil &amp; Gas Intelligence</title>
<link href="https://fonts.googleapis.com/css2?family=Poppins:wght@400;500;600;700&display=swap" rel="stylesheet">
<style>
:root{
  --orange:#e8642a;
  --navy:#1c1733;
  --ink:#1d1d22;
  --muted:#4a4a52;
  --light:#ececec;
  --white:#ffffff;
}
*{box-sizing:border-box;margin:0;padding:0}
html,body{width:1200px;height:4141px;overflow:hidden}
body{font-family:'Poppins',sans-serif;color:var(--ink);background:var(--white);position:relative}
.abs{position:absolute}
.btn{position:absolute;display:flex;align-items:center;justify-content:center;border-radius:30px;font-weight:600;font-size:16px;text-decoration:none}
.btn-orange{background:var(--orange);color:var(--white)}
.btn-outline{border:2px solid var(--ink);color:var(--ink);background:var(--white)}
.ph{position:absolute}

/* header */
.site-header{position:absolute;left:0;top:0;width:1200px;height:130px;background:var(--white)}
.brand{position:absolute;left:75px;top:16px;width:182px;height:101px;display:flex;flex-direction:column;align-items:center;justify-content:center;gap:8px}
.brand-mark{width:52px;height:52px;border-radius:50%;background:var(--ink)}
.brand-name{font-size:13px;font-weight:700;letter-spacing:2px;color:var(--ink)}
.lang{position:absolute;left:1065px;top:58px;display:flex;align-items:center;gap:8px;font-size:13px;font-weight:600}
.main-nav{position:absolute;left:0;top:130px;width:1200px;height:53px;background:var(--navy);display:flex;align-items:center;padding-left:93px;gap:37px}
.main-nav a{color:var(--white);font-size:12px;font-weight:600;text-decoration:none;letter-spacing:.2px}
.main-nav a.active{color:var(--orange);text-decoration:underline;text-underline-offset:6px}

/* hero */
.hero{position:absolute;left:0;top:183px;width:1200px;height:590px;background:linear-gradient(100deg,#0d1a22 0%,#15303a 40%,#4a4a45 70%,#c98742 100%)}
.hero h1{position:absolute;left:75px;top:130px;font-size:37px;line-height:43px;color:var(--white);font-weight:700;width:640px}
.hero p{position:absolute;left:75px;top:272px;width:590px;font-size:16px;line-height:28px;color:var(--white)}

/* about */
.about-img{left:75px;top:843px;width:600px;height:354px;border-radius:177px;background:linear-gradient(135deg,#2c4466,#6b6a66 60%,#b7772f)}
.section-title{font-size:42px;font-weight:500;color:var(--ink)}
.section-title b{font-weight:700}
.about-text{position:absolute;left:703px;top:860px;width:430px}
.about-text p{font-size:14.5px;line-height:24px;color:var(--muted);margin-top:12px}
.about-text p:first-of-type{margin-top:28px}

/* access */
.access{position:absolute;left:0;top:1269px;width:1200px;height:515px;background:var(--light)}
.access .section-title{position:absolute;left:0;top:48px;width:1200px;text-align:center}
.card{position:absolute;top:130px;width:241px;height:246px;background:var(--white);border-radius:14px;text-align:center;padding-top:25px}
.card.featured{background:linear-gradient(180deg,var(--navy) 30%,var(--orange) 100%);color:var(--white)}
.card .icon{width:72px;height:72px;border-radius:50%;background:var(--orange);margin:0 auto;display:flex;align-items:center;justify-content:center}
.card.featured .icon{background:#e9683a}
.card h3{font-size:16px;line-height:20px;font-weight:600;margin-top:20px}
.card p{font-size:12.5px;line-height:20px;margin:12px auto 0;width:200px;color:var(--muted)}
.card.featured p{color:var(--white)}
.dots{position:absolute;top:444px;left:504px;display:flex;gap:10px}
.dots span{width:58px;height:3px;background:#bdbdbd}
.dots span.on{background:var(--orange)}

/* why */
.why-title{left:75px;top:1870px}
.why-item{position:absolute;left:75px;width:540px;display:flex}
.why-item .num{flex:0 0 97px;font-size:66px;line-height:66px;color:var(--orange);font-weight:400}
.why-item h4{font-size:19px;font-weight:600;margin-top:-2px}
.why-item p{font-size:12.5px;line-height:20px;color:var(--muted);margin-top:6px}
.why-img{left:675px;top:1855px;width:450px;height:397px;border-radius:22px;background:linear-gradient(160deg,#6c7b91,#9aa1a4 45%,#9ccc2d 85%)}

/* how */
.how{position:absolute;left:0;top:2327px;width:1200px;height:463px;background:linear-gradient(180deg,#1c1733,#2a2244 60%,#3a2b49)}
.how h2{position:absolute;top:135px;width:1200px;text-align:center;font-size:42px;font-weight:500;color:var(--white)}
.how h2 b{font-weight:700}
.how p{position:absolute;top:212px;left:170px;width:860px;text-align:center;font-size:18.5px;line-height:28.5px;color:#e9e7ef}

/* news */
.news-title{left:75px;top:2845px}
.arrow{position:absolute;top:2861px;width:25px;height:25px;border-radius:50%;display:flex;align-items:center;justify-content:center}
.news-card{position:absolute;top:2921px;width:328px}
.news-card .thumb{height:211px;border-radius:10px}
.news-card .date{font-size:13px;color:var(--orange);margin-top:20px}
.news-card h5{font-size:22.5px;line-height:31px;font-weight:500;margin-top:4px}
.news-card h5 span{display:block;white-space:nowrap;overflow:hidden;text-overflow:ellipsis}

/* cta */
.cta{position:absolute;left:0;top:3414px;width:1200px;height:386px;background:linear-gradient(90deg,#1d1935,#2c2648 50%,#3b3152)}
.cta h2{position:absolute;top:68px;width:1200px;text-align:center;font-size:44px;line-height:50px;font-weight:500;color:var(--white)}
.cta h2 b{font-weight:700}
.cta p{position:absolute;top:186px;left:180px;width:840px;text-align:center;font-size:18.5px;line-height:29px;color:#e9e7ef}

/* footer */
.site-footer{position:absolute;left:0;top:3800px;width:1200px;height:341px;background:var(--white)}
.foot-brand{position:absolute;left:85px;top:60px;width:230px;display:flex;flex-direction:column;align-items:center;gap:10px}
.copy{position:absolute;left:85px;top:213px;width:230px;text-align:center;font-size:13.5px;line-height:21px}
.foot-col{position:absolute;top:64px}
.foot-col h6{font-size:20px;font-weight:600;margin-bottom:8px}
.foot-col a,.foot-col span{display:block;font-size:12.5px;line-height:27px;color:var(--ink);text-decoration:none}
.foot-col a.mail{color:var(--orange);text-decoration:underline;font-weight:600}
.socials{position:absolute;left:885px;top:200px;display:flex;gap:28px}
.socials span{width:20px;height:20px;background:var(--ink);border-radius:4px}
.socials span:first-child{background:var(--orange)}
.chat{position:absolute;left:1096px;top:4040px;width:67px;height:67px;border-radius:50%;background:var(--navy);display:flex;align-items:center;justify-content:center}
</style>
</head>
<body>

<header class="site-header">
  <div class="brand">
    <div class="brand-mark"></div>
    <div class="brand-name">TARNOVEX CO</div>
  </div>
  <a class="btn btn-orange" style="left:707px;top:43px;width:162px;height:52px">Register Now</a>
  <a class="btn btn-outline" style="left:883px;top:43px;width:153px;height:52px">Contact Us</a>
  <div class="lang">
    <svg width="18" height="18" viewBox="0 0 24 24" fill="none" stroke="#1d1d22" stroke-width="2"><circle cx="12" cy="12" r="10"/><path d="M2 12h20M12 2c3 3 3 17 0 20M12 2c-3 3-3 17 0 20"/></svg>
    EN
    <svg width="8" height="12" viewBox="0 0 8 12" fill="#1d1d22"><path d="M4 0l4 5H0zM4 12L0 7h8z"/></svg>
  </div>
</header>

<nav class="main-nav">
  <a class="active">HOME</a>
  <a>INDUSTRY INSIGHTS</a>
  <a>OIL &amp; GAS OPPORTUNITIES</a>
  <a>SUPPLIER &amp; COMPANY NETWORK</a>
  <a>NEWS</a>
  <a>REGISTER</a>
  <a>LEGAL FRAMEWORK</a>
</nav>

<section class="hero" role="img" aria-label="Offshore oil platform at sunset over the sea with glowing digital circuit lines">
  <h1>Access Mozambique’s<br>Oil &amp; Gas Industry Intelligence<br>in One Platform</h1>
  <p>Tarnovex is a modern online connection and consulting platform designed to facilitate access to the Mozambican Oil and Gas Industry through premium industry insights, supplier information, tenders, legal frameworks, and strategic project data.</p>
  <a class="btn btn-orange" style="left:75px;top:402px;width:179px;height:53px">Register Now</a>
</section>

<div class="ph about-img" role="img" aria-label="Engineer in hard hat holding a tablet in front of a lit offshore platform at dusk"></div>
<div class="about-text">
  <h2 class="section-title">What is <b>Tarnovex?</b></h2>
  <p>Tarnovex is a unique online platform built to connect businesses, investors, suppliers, and professionals with valuable information about the Mozambican Oil &amp; Gas sector.</p>
  <p>Through a secure digital paywall system, users gain access to organized, up-to-date, and carefully selected industry information that supports better decision-making, market understanding, and business opportunities within Mozambique’s growing hydrocarbons industry.</p>
</div>

<section class="access">
  <h2 class="section-title">What You <b>Will Access</b></h2>
  <div class="card featured" style="left:75px">
    <div class="icon"><svg width="36" height="36" viewBox="0 0 24 24" fill="none" stroke="#fff" stroke-width="1.6"><path d="M12 3c3 4 5 7 5 10a5 5 0 0 1-10 0c0-3 2-6 5-10z"/></svg></div>
    <h3>Hydrocarbon Industry<br>Information</h3>
    <p>General information and insights about Mozambique’s oil and gas sector.</p>
  </div>
  <div class="card" style="left:345px">
    <div class="icon"><svg width="36" height="36" viewBox="0 0 24 24" fill="none" stroke="#fff" stroke-width="1.6"><path d="M12 3v6M9 9h6l2 12H7zM5 21h14"/></svg></div>
    <h3>Main Gas<br>Projects</h3>
    <p>Details about major gas and energy projects operating in Mozambique.</p>
  </div>
  <div class="card" style="left:615px">
    <div class="icon"><svg width="36" height="36" viewBox="0 0 24 24" fill="none" stroke="#fff" stroke-width="1.6"><rect x="4" y="4" width="4" height="4"/><rect x="10" y="4" width="4" height="4"/><rect x="16" y="4" width="4" height="4"/><path d="M4 12h16v8H4z"/></svg></div>
    <h3>Supplier &amp; Company<br>Database</h3>
    <p>Mozambican companies capable of meeting Level 3 supply requirements.</p>
  </div>
  <div class="card" style="left:885px">
    <div class="icon"><svg width="36" height="36" viewBox="0 0 24 24" fill="none" stroke="#fff" stroke-width="1.6"><path d="M3 21h18M5 21V11l5 3V11l5 3V5h4v16"/></svg></div>
    <h3>Industry<br>Contacts</h3>
    <p>Key contacts from NOCs, Operators, EPCs, and Second-Tier Suppliers.</p>
  </div>
  <div class="dots"><span class="on"></span><span></span><span></span></div>
</section>

<h2 class="abs section-title why-title">Why <b>Tarnovex Is Unique</b></h2>
<div class="why-item" style="top:1955px"><div class="num">01</div><div><h4>Up-to-Date Industry Intelligence</h4><p>Receive frequent updates about developments in Mozambique’s Oil &amp; Gas sector.</p></div></div>
<div class="why-item" style="top:2053px"><div class="num">02</div><div><h4>High-Quality Curated Information</h4><p>Access carefully selected and synthesized information tailored to industry stakeholders.</p></div></div>
<div class="why-item" style="top:2151px"><div class="num">03</div><div><h4>Time-Saving Access</h4><p>Avoid spending hours searching through scattered online sources with organized and accessible content in one platform.</p></div></div>
<div class="ph why-img" role="img" aria-label="Three engineers in hard hats and high-visibility jackets reviewing a laptop outdoors"></div>

<section class="how" role="img" aria-label="Silhouette of an industrial plant against a dusk sky with dark purple overlay">
  <h2>How The <b>Platform Works</b></h2>
  <p>The platform operates through a secure automated payment system that grants registered users access to premium and exclusive content. By subscribing, users receive organized industry intelligence designed to save time, improve market access, and support strategic business growth within Mozambique’s energy sector.</p>
</section>

<h2 class="abs section-title news-title">Latest <b>News</b></h2>
<div class="arrow" style="left:1064px;background:var(--ink)"><svg width="14" height="14" viewBox="0 0 24 24" fill="none" stroke="#fff" stroke-width="3"><path d="M20 12H5M11 6l-6 6 6 6"/></svg></div>
<div class="arrow" style="left:1103px;background:var(--orange)"><svg width="14" height="14" viewBox="0 0 24 24" fill="none" stroke="#fff" stroke-width="3"><path d="M4 12h15M13 6l6 6-6 6"/></svg></div>

<article class="news-card" style="left:75px">
  <div class="thumb" role="img" aria-label="Engineer with a laptop in front of a refinery" style="background:linear-gradient(135deg,#8fb6d8,#c6c9cb 55%,#e07a35)"></div>
  <div class="date">Jun 30, 2026</div>
  <h5><span>Duis aute irure dolor in</span><span>reprehenderit in voluptate velit</span></h5>
</article>
<article class="news-card" style="left:437px">
  <div class="thumb" role="img" aria-label="Two workers inspecting pipes at an industrial site" style="background:linear-gradient(135deg,#5d6669,#8e948f 50%,#b5d33c)"></div>
  <div class="date">Jun 30, 2026</div>
  <h5><span>Duis aute irure dolor in</span><span>reprehenderit in voluptate velit</span></h5>
</article>
<article class="news-card" style="left:798px">
  <div class="thumb" role="img" aria-label="Offshore platform with digital network overlay" style="background:linear-gradient(135deg,#3f7fbf,#2a5f97 55%,#e0a43a)"></div>
  <div class="date">Jun 30, 2026</div>
  <h5><span>Duis aute irure dolor in</span><span>reprehenderit in voluptate velit</span></h5>
</article>
<a class="btn btn-outline" style="left:511px;top:3283px;width:178px;height:53px">View All News</a>

<section class="cta" role="img" aria-label="Worker silhouette at an industrial plant at dusk with dark overlay">
  <h2>Start Exploring Mozambique’s<br><b>Oil &amp; Gas Opportunities</b></h2>
  <p>Register today to access premium industry information, supplier networks, tenders, and strategic market insights through Tarnovex.</p>
  <a class="btn btn-orange" style="left:408px;top:262px;width:177px;height:53px">Register Now</a>
  <a class="btn btn-orange" style="left:618px;top:262px;width:179px;height:53px">Contact Us</a>
</section>

<footer class="site-footer">
  <div class="foot-brand">
    <div class="brand-mark" style="width:58px;height:58px"></div>
    <div class="brand-name">TARNOVEX CO</div>
  </div>
  <div class="copy">Copyright © 2026 by Tarnovex Co.<br>All Rights Reserved.</div>
  <div class="foot-col" style="left:352px">
    <h6>Quick Links</h6>
    <a>Home</a><a>Industry Insights</a><a>Oil &amp; Gas Opportunities</a><a>Supplier &amp; Company Network</a><a>News</a><a>Register</a><a>Legal Framework</a>
  </div>
  <div class="foot-col" style="left:615px">
    <h6>Industry Insights</h6>
    <a>Local Content Legal Framework</a><a>Hydrocarbons Information</a><a>O&amp;G Ownership &amp; Access</a><a>Mozambican Oil &amp; Gas Books</a>
  </div>
  <div class="foot-col" style="left:885px;width:260px">
    <h6>Contact Us</h6>
    <span style="line-height:22px">18 Kestrel Ridge Road<br>Vanterburg, Highveld South Africa</span>
    <a class="mail" style="margin-top:6px">contacto@tarnovexmz.org</a>
  </div>
  <div class="socials"><span></span><span></span><span></span><span></span></div>
</footer>

<div class="chat"><svg width="30" height="30" viewBox="0 0 24 24" fill="#fff"><path d="M4 4h12a2 2 0 0 1 2 2v7a2 2 0 0 1-2 2H9l-4 3v-3H4a2 2 0 0 1-2-2V6a2 2 0 0 1 2-2z"/><path d="M20 8h1a1 1 0 0 1 1 1v7a1 1 0 0 1-1 1h-1v3l-4-3h-5v-1h7V8z" opacity=".7"/></svg></div>

</body>
</html>
```